Business Card Design needed for start up company Halvora

In need of a new business card designed for a start up company based in Sydney, Halvora is a new start up innovative Company, our mission it to make property accessible for everyday Australian and to become the leading Real Estate platform in Australia. We want it to be fresh and clean.

Industry/Entity Type

Financial

Contact Information for Business Card

Section for Name
Section for Title

HALVORA - The Strength of Pooling
Mobile:
Direct:

Font styles to use
Sans Serif

Colors
33a6d7
0692cd
0255a3
ffffff

Requirements
Must have
• Logo, all business card details

```html
<!DOCTYPE html>
<html lang="en">
<head>
<meta charset="utf-8">
<title>Halvora Business Card</title>
<link rel="stylesheet" href="https://fonts.googleapis.com/css2?family=Open+Sans:wght@400;600;700;800&display=swap">
<style>
  :root {
    --backdrop: #8a8a8a;
    --card-light: #ececec;
    --brand-sky: #259fda;
    --brand-cyan: #1a8fd0;
    --brand-navy: #1e3f7a;
    --card-navy: #204a80;
    --text-grey: #444444;
    --white: #ffffff;
  }
  * { margin: 0; padding: 0; box-sizing: border-box; }
  html, body {
    width: 1200px;
    height: 900px;
    overflow: hidden;
  }
  body {
    position: relative;
    background: var(--backdrop);
    font-family: "Open Sans", Arial, sans-serif;
  }
  .card {
    position: absolute;
    top: 170px;
    width: 347px;
    height: 561px;
  }
  .card-front { left: 259px; background: var(--card-light); }
  .card-back { left: 631px; background: var(--card-navy); }

  .brand-lockup {
    position: absolute;
    left: 27px;
    top: 93px;
    display: flex;
    align-items: center;
    gap: 8px;
  }
  .brand-dot {
    width: 88px;
    height: 88px;
    border-radius: 50%;
    background: var(--brand-sky);
  }
  .brand-name {
    font-weight: 800;
    font-size: 41px;
    line-height: 1;
    color: var(--brand-navy);
    letter-spacing: -0.5px;
  }
  .tagline {
    position: absolute;
    top: 199px;
    width: 100%;
    text-align: center;
    font-weight: 600;
    font-size: 17px;
    color: var(--brand-cyan);
  }
  .contact-block {
    position: absolute;
    top: 384px;
    width: 100%;
    text-align: center;
    color: var(--text-grey);
  }
  .person-name {
    font-weight: 600;
    font-size: 20px;
    line-height: 28px;
  }
  .person-name .first { color: var(--brand-cyan); }
  .person-name .last { color: var(--brand-navy); }
  .person-title {
    font-size: 15px;
    line-height: 22px;
    margin-bottom: 14px;
  }
  .contact-line {
    font-size: 15px;
    line-height: 20px;
  }
  .contact-line .label {
    font-weight: 700;
    color: var(--brand-cyan);
  }

  .back-emblem {
    position: absolute;
    left: 74px;
    top: 181px;
    width: 199px;
    height: 199px;
    border-radius: 50%;
    background: var(--white);
  }
  .back-url {
    position: absolute;
    top: 447px;
    width: 100%;
    text-align: center;
    font-weight: 700;
    font-size: 17px;
    color: var(--white);
  }
</style>
</head>
<body>
  <section class="card card-front">
    <div class="brand-lockup">
      <div class="brand-dot"></div>
      <div class="brand-name">HALVORA</div>
    </div>
    <p class="tagline">THE STRENGTH OF POOLING</p>
    <div class="contact-block">
      <p class="person-name"><span class="first">DANIEL</span> <span class="last">HARPER</span></p>
      <p class="person-title">Managing Director</p>
      <p class="contact-line"><span class="label">P:</span> 044-987 654 321</p>
      <p class="contact-line"><span class="label">M:</span> 044-987 654 322</p>
      <p class="contact-line"><span class="label">E:</span> hello@halvora.com</p>
    </div>
  </section>

  <section class="card card-back">
    <div class="back-emblem"></div>
    <p class="back-url">WWW.HALVORA.COM</p>
  </section>
</body>
</html>
```